Flowmark Engineering Business Card

our company has just rebranded and taken on a new logo design. We now need to update our business cards with the new logo. This is also an opportunity to reformat and modernize our look. We are an engineering company so the look needs to be formal and professional yet it should look modern. Have a look at our current card and the new card should have the same information.

Target Market(s)

Engineering firms, government, mining companies

Industry/Entity Type

Mechanical Engineering

Contact Information for Business Card

see example attached

Requirements
Must have
• look professional and modern
Should not have
• should not include the office locations 'Brisbane, Sydney and Kuala Lumpur'
• you will find this on the example but it should not be included in these versions. please remove from your submissions and resubmit

```html
<!DOCTYPE html>
<html lang="en">
<head>
<meta charset="utf-8">
<title>Flowmark Engineering Business Card</title>
<link rel="stylesheet" href="https://fonts.googleapis.com/css2?family=Open+Sans:wght@400;600;700&display=swap">
<style>
  :root {
    --page-bg: #d9d9da;
    --card-bg: #ffffff;
    --brand-blue: #3a47a6;
    --accent-teal: #3fbfcf;
    --text-grey: #5c5c5c;
    --card-shadow: rgba(0, 0, 0, 0.18);
  }
  * { box-sizing: border-box; margin: 0; padding: 0; }
  html, body {
    width: 1200px;
    height: 902px;
    overflow: hidden;
    background: var(--page-bg);
    font-family: "Open Sans", Arial, sans-serif;
  }
  .sheet {
    position: relative;
    width: 1200px;
    height: 902px;
  }
  .card {
    position: absolute;
    left: 290px;
    width: 620px;
    height: 354px;
    background: var(--card-bg);
    box-shadow: 0 6px 18px var(--card-shadow);
  }
  .card--front { top: 56px; }
  .card--back { top: 490px; }

  .brand {
    display: flex;
    align-items: center;
    gap: 14px;
    color: var(--brand-blue);
    font-weight: 700;
    text-transform: uppercase;
  }
  .brand__dot {
    width: 58px;
    height: 58px;
    border-radius: 50%;
    background: var(--brand-blue);
    flex: none;
  }
  .brand__name {
    line-height: 1.05;
  }
  .brand__line-main {
    display: block;
    font-size: 40px;
    letter-spacing: 1px;
  }
  .brand__line-sub {
    display: block;
    font-size: 17px;
    letter-spacing: 6px;
    padding-left: 22px;
  }

  .card--front .brand {
    position: absolute;
    left: 50%;
    top: 50%;
    transform: translate(-50%, -50%);
  }

  .card--back .brand {
    position: absolute;
    left: 46px;
    top: 124px;
  }
  .card--back .brand__dot { width: 46px; height: 46px; }
  .card--back .brand__line-main { font-size: 32px; }
  .card--back .brand__line-sub { font-size: 14px; letter-spacing: 5px; padding-left: 18px; }

  .person {
    position: absolute;
    right: 46px;
    top: 44px;
    text-align: right;
  }
  .person__name {
    color: var(--accent-teal);
    font-weight: 600;
    font-size: 21px;
  }
  .person__role {
    color: var(--text-grey);
    font-size: 19px;
  }

  .website {
    position: absolute;
    right: 46px;
    top: 176px;
    font-size: 15px;
    letter-spacing: 3px;
    color: var(--text-grey);
  }
  .website__domain {
    color: var(--accent-teal);
    font-weight: 600;
  }

  .contact {
    position: absolute;
    left: 46px;
    bottom: 30px;
    list-style: none;
    font-size: 14px;
    color: var(--text-grey);
    line-height: 1.7;
  }
  .contact__item {
    display: flex;
    align-items: center;
    gap: 8px;
  }
  .contact__icon {
    width: 13px;
    height: 13px;
    flex: none;
    fill: var(--accent-teal);
  }
  .contact__spacer { width: 13px; flex: none; }
</style>
</head>
<body>
<main class="sheet">
  <section class="card card--front" aria-label="Business card front">
    <div class="brand">
      <span class="brand__dot"></span>
      <span class="brand__name">
        <span class="brand__line-main">Flowmark</span>
        <span class="brand__line-sub">Engineering</span>
      </span>
    </div>
  </section>

  <section class="card card--back" aria-label="Business card back">
    <div class="person">
      <p class="person__name">Dana Whitfield</p>
      <p class="person__role">Owner</p>
    </div>

    <p class="website">www.<span class="website__domain">flowmarkeng</span>.com</p>

    <div class="brand">
      <span class="brand__dot"></span>
      <span class="brand__name">
        <span class="brand__line-main">Flowmark</span>
        <span class="brand__line-sub">Engineering</span>
      </span>
    </div>

    <ul class="contact">
      <li class="contact__item">
        <svg class="contact__icon" viewBox="0 0 24 24" aria-hidden="true"><path d="M6.6 10.8a15.1 15.1 0 0 0 6.6 6.6l2.2-2.2c.3-.3.7-.4 1-.2 1.1.4 2.3.6 3.6.6.6 0 1 .4 1 1V20c0 .6-.4 1-1 1A17 17 0 0 1 3 4c0-.6.4-1 1-1h3.5c.6 0 1 .4 1 1 0 1.3.2 2.5.6 3.6.1.3 0 .7-.2 1z"/></svg>
        <span>512.000.4179</span>
      </li>
      <li class="contact__item">
        <svg class="contact__icon" viewBox="0 0 24 24" aria-hidden="true"><path d="M2 5h20v14H2z M2 5l10 7 10-7" stroke="#fff" stroke-width="1.6"/></svg>
        <span>dana@flowmarkeng.com</span>
      </li>
      <li class="contact__item">
        <span class="contact__spacer"></span>
        <span>2280 Cedar Ridge Ln Austin TX 78750</span>
      </li>
    </ul>
  </section>
</main>
</body>
</html>
```